KPV Datacore Solutions

We need a Logo and Website for our company based in London. We are a IT recruitment company . We provide quality resources to top IT company across UK.

Industry/Entity Type

It Company

Number of Pages Required

4 page

```html
<!DOCTYPE html>
<html lang="en">
<head>
<meta charset="utf-8">
<title>KPV Datacore Solutions – IT Recruitment</title>
<link href="https://fonts.googleapis.com/css2?family=Open+Sans:wght@400;600;700&display=swap" rel="stylesheet">
<style>
:root{
  --red:#c8202a;
  --red-dark:#a9161f;
  --ink:#333;
  --muted:#666;
  --topbar:#2c2c2c;
  --footer:#3a3a3a;
  --light:#f4f4f4;
  --line:#e2e2e2;
}
*{box-sizing:border-box;margin:0;padding:0}
html,body{width:1200px;height:2161px;overflow:hidden}
body{font-family:"Open Sans",Arial,sans-serif;color:var(--ink);background:#fff;font-size:11px;line-height:1.7}
.wrap{width:880px;margin:0 auto;position:relative}
.accent{color:var(--red)}
.btn{display:inline-flex;align-items:center;gap:5px;background:var(--red);color:#fff;font-weight:700;font-size:10px;padding:0 12px;height:36px;border-radius:2px;text-transform:uppercase}
.btn svg{width:10px;height:10px}

/* top bar */
.topbar{height:33px;background:var(--topbar);color:#bbb;font-size:10px}
.topbar .wrap{display:flex;align-items:center;justify-content:space-between;height:33px}
.topbar .contact{display:flex;gap:24px}
.topbar .contact span{display:flex;align-items:center;gap:5px}
.topbar .social{display:flex;gap:7px}
.topbar .social i{width:15px;height:15px;border-radius:50%;background:#555;display:block}
.topbar .social i.search{background:var(--red)}

/* header */
.header{height:92px;border-bottom:3px solid var(--red)}
.header .wrap{display:flex;align-items:center;justify-content:space-between;height:89px}
.brand{display:flex;align-items:center;gap:8px;font-size:19px;color:#333}
.brand .dot{width:16px;height:16px;border-radius:50%;background:var(--red)}
.nav{display:flex;gap:32px;font-size:11px;color:#333;align-items:center}
.nav .home{width:11px;height:11px}

/* hero */
.hero{height:503px;background:linear-gradient(90deg,#1e2a35 0%,#2c3a46 45%,#6d727a 70%,#3a4450 100%);position:relative}
.hero .wrap{padding-top:160px}
.hero h1{font-size:33px;font-weight:400;color:#fff;line-height:1.2;margin-bottom:22px}
.hero h1 b{font-weight:700}
.hero p{color:#e6e6e6;width:390px;font-size:10.5px;line-height:1.8;margin-bottom:22px}
.hero .dots{position:absolute;left:568px;top:450px;display:flex;gap:4px}
.hero .dots i{width:10px;height:10px;border-radius:50%;background:#fff;display:block}
.hero .dots i.on{background:var(--red)}

/* search band */
.search{height:184px;background:var(--red);color:#fff}
.search .wrap{display:flex;height:184px;padding-top:20px}
.search .col{width:440px}
.search .col + .col{border-left:1px solid rgba(255,255,255,.25);padding-left:32px}
.search .col:first-child{padding-right:32px}
.search h2{font-size:23px;font-weight:400;margin-bottom:8px}
.search p{font-size:10.5px;line-height:1.75;margin-bottom:16px}
.search .field{display:flex;gap:4px}
.search .select{flex:1;height:38px;background:#fff;color:#777;font-size:10px;display:flex;align-items:center;justify-content:space-between;padding:0 12px;border-radius:2px}
.search .go{width:44px;height:38px;border:1px solid #fff;display:flex;align-items:center;justify-content:center;font-weight:700;font-size:12px;border-radius:2px}

/* intro */
.intro{text-align:center;padding-top:40px}
.intro h2{font-size:22px;font-weight:400;margin-bottom:12px}
.intro .lead{font-size:10.5px;color:var(--muted);width:580px;margin:0 auto}
.features{display:flex;justify-content:space-between;margin-top:46px;text-align:left}
.feature{display:flex;gap:20px;width:280px}
.feature .ring{flex:none;width:90px;height:90px;border:2px solid var(--red);border-radius:50%;display:flex;align-items:center;justify-content:center}
.feature .ring svg{width:30px;height:30px}
.feature .text{flex:1;min-width:0}
.feature h3{font-size:14px;font-weight:400;margin:-2px 0 6px}
.feature p{font-size:10.5px;color:var(--muted);line-height:1.75;width:auto;margin:0}
.divider{border-top:1px solid var(--line);margin-top:46px}

/* about */
.about{display:flex;gap:38px;padding-top:36px;height:320px}
.about .photo{flex:none;width:359px;height:233px;border:1px solid #ddd;background:linear-gradient(90deg,#eef1f4,#cfd5dc 50%,#8a8f96)}
.about h2{font-size:22px;font-weight:400;margin-bottom:10px}
.about p{font-size:10.5px;color:var(--muted);line-height:1.8;margin-bottom:18px}

/* recruitments */
.recent{background:var(--light);height:376px;padding-top:28px;border-top:1px solid var(--line)}
.recent h2{font-size:22px;font-weight:400;margin-bottom:14px}
.cards{display:flex;justify-content:space-between}
.card{width:202px;height:252px;background:#fff;border:1px solid #e3e3e3}
.card .photo{height:122px;background:linear-gradient(135deg,#d9dde2,#8e97a1)}
.card:nth-child(2) .photo{background:linear-gradient(135deg,#c9d6dc,#5f6d78)}
.card:nth-child(3) .photo{background:linear-gradient(135deg,#e3e7ea,#6b7783)}
.card:nth-child(4) .photo{background:linear-gradient(135deg,#b9c7d3,#3c4a57)}
.card .body{padding:12px 12px}
.card h4{font-size:13px;font-weight:600;margin-bottom:6px}
.card p{font-size:10px;color:var(--muted);line-height:1.8;margin-bottom:8px}
.card .loc{color:var(--red);font-size:10px;display:flex;align-items:center;gap:3px}
.card .loc svg{width:8px;height:10px}

/* clients */
.clients{height:102px;border-top:1px solid var(--line);display:flex;align-items:center}
.clients .wrap{display:flex;align-items:center;justify-content:space-between}
.clients .arrow{width:12px;height:22px}
.clients .logos{display:flex;justify-content:space-around;flex:1;padding:0 40px}
.clients .logos span{font-size:17px;font-weight:600;color:#888;letter-spacing:.5px}

/* footer */
.footer{height:196px;background:var(--footer);color:#bbb}
.footer .wrap{display:flex;padding-top:30px}
.footer h4{font-size:14px;font-weight:400;color:#fff;margin-bottom:12px}
.footer .about-col{width:250px;font-size:10.5px;line-height:1.8;padding-right:20px}
.footer .contact-col{width:196px;font-size:10.5px}
.footer .contact-col li{list-style:none;display:flex;gap:6px;margin-bottom:6px;line-height:1.7}
.footer .contact-col svg{flex:none;width:9px;height:10px;margin-top:4px}
.footer .map{width:434px;height:128px;border:2px solid #888;background:linear-gradient(135deg,#cde1ef,#f0ece2 55%,#bcd6ea)}
.bottom{height:58px;background:var(--red);color:#fff;font-size:10px}
.bottom .wrap{display:flex;align-items:center;justify-content:space-between;height:58px}
.bottom .social{display:flex;gap:5px}
.bottom .social i{width:28px;height:28px;border:2px solid #fff;border-radius:50%;display:block}
</style>
</head>
<body>

<div class="topbar">
  <div class="wrap">
    <div class="contact">
      <span><svg width="9" height="9" viewBox="0 0 10 10"><path d="M2 0h2l1 3-1.5 1a6 6 0 0 0 2.5 2.5L7 5l3 1v2a2 2 0 0 1-2 2A8 8 0 0 1 0 2a2 2 0 0 1 2-2z" fill="#aaa"/></svg>555-310-7284</span>
      <span><svg width="10" height="8" viewBox="0 0 10 8"><rect width="10" height="8" fill="#aaa"/><path d="M0 0l5 4 5-4" stroke="#2c2c2c" fill="none"/></svg>info@kpvdatacoresolutions.com</span>
    </div>
    <div class="social"><i></i><i></i><i></i><i></i><i></i><i></i><i></i><i class="search"></i></div>
  </div>
</div>

<header class="header">
  <div class="wrap">
    <div class="brand"><span class="dot"></span>KPV Datacore Solutions</div>
    <nav class="nav">
      <svg class="home" viewBox="0 0 12 12"><path d="M6 0l6 6h-2v6H7V8H5v4H2V6H0z" fill="#c8202a"/></svg>
      <span>About Us</span><span>Industry Practices</span><span>Client Services</span><span>Job Seekers</span><span>Recruitment Process</span><span>Join us</span>
    </nav>
  </div>
</header>

<section class="hero" role="img" aria-label="Hand drawing a red circle around a person icon among a network of people">
  <div class="wrap">
    <h1><b>KPV</b> Datacore Solutions</h1>
    <p>Lorem ipsum dolor sit amet, consectetur adipiscing elit, sed do eiusmod tempor incididunt ut labore et dolore magna aliquaenim ad minim veniam, quis nostrud exercitation ullamco laboris nisi ut aliquip ex ea commodo.</p>
    <span class="btn">Read more <svg viewBox="0 0 10 10"><circle cx="5" cy="5" r="4.3" stroke="#fff" fill="none"/><path d="M4 3l2 2-2 2" stroke="#fff" fill="none"/></svg></span>
  </div>
  <div class="dots"><i></i><i></i><i class="on"></i><i></i><i></i></div>
</section>

<section class="search">
  <div class="wrap">
    <div class="col">
      <h2>Jobseekers</h2>
      <p>Lorem ipsum dolor sit amet, consectetur adipiscing elit, sed do eiusmod tempor incididunt ut labore et dolore magna aliquaenim ad minim veniam</p>
      <div class="field"><div class="select">Choose location<svg width="12" height="7" viewBox="0 0 12 7"><path d="M0 0h12L6 7z" fill="#999"/></svg></div><div class="go">GO</div></div>
    </div>
    <div class="col">
      <h2>Employers</h2>
      <p>Lorem ipsum dolor sit amet, consectetur adipiscing elit, sed do eiusmod tempor incididunt ut labore et dolore magna aliquaenim ad minim veniam</p>
      <div class="field"><div class="select">Choose location<svg width="12" height="7" viewBox="0 0 12 7"><path d="M0 0h12L6 7z" fill="#999"/></svg></div><div class="go">GO</div></div>
    </div>
  </div>
</section>

<section class="intro">
  <div class="wrap">
    <h2><span class="accent">KPV</span> Datacore Solutions-The Recruitment Company</h2>
    <p class="lead">Lorem ipsum dolor sit amet, consectetur adipiscing elit, sed do eiusmod tempor incididunt ut labore et dolore magna aliquaenim ad minim veniam, quis nostrud exercitation ullamco laboris nisi ut aliquip ex ea commodo cequat.</p>
    <div class="features">
      <div class="feature">
        <div class="ring"><svg viewBox="0 0 30 30"><g fill="#c8202a"><rect x="3" y="6" width="4" height="4"/><rect x="9" y="6" width="18" height="4"/><rect x="3" y="13" width="4" height="4"/><rect x="9" y="13" width="18" height="4"/><rect x="3" y="20" width="4" height="4"/><rect x="9" y="20" width="18" height="4"/></g></svg></div>
        <div class="text"><h3>Category We Serve</h3><p>Lorem ipsulom dolor sit amecon se ctetur adipiscing elitloised eiu smod tempor incididun.</p></div>
      </div>
      <div class="feature">
        <div class="ring"><svg viewBox="0 0 30 30"><circle cx="14" cy="16" r="11" fill="#c8202a"/><path d="M8 12l4 2-1 4 3 3M17 9l3 4-2 3 3 2" stroke="#fff" stroke-width="1.5" fill="none"/><circle cx="23" cy="7" r="5" fill="#c8202a" stroke="#fff"/><circle cx="23" cy="7" r="1.8" fill="#fff"/></svg></div>
        <div class="text"><h3>Major Locations</h3><p>Lorem ipsulom dolor sit amecon se ctetur adipiscing elitloised eiu smod tempor incididun.</p></div>
      </div>
      <div class="feature">
        <div class="ring"><svg viewBox="0 0 30 30"><rect x="8" y="3" width="14" height="24" fill="#c8202a"/><g fill="#fff"><rect x="11" y="6" width="3" height="3"/><rect x="16" y="6" width="3" height="3"/><rect x="11" y="11" width="3" height="3"/><rect x="16" y="11" width="3" height="3"/><rect x="11" y="16" width="3" height="3"/><rect x="16" y="16" width="3" height="3"/><rect x="13" y="21" width="4" height="6"/></g></svg></div>
        <div class="text"><h3>Major Companies</h3><p>Lorem ipsulom dolor sit amecon se ctetur adipiscing elitloised eiu smod tempor incididun.</p></div>
      </div>
    </div>
    <div class="divider"></div>
  </div>
</section>

<section class="wrap about">
  <div class="photo" role="img" aria-label="Row of smiling business professionals in suits"></div>
  <div>
    <h2>About <span class="accent">KPV</span> Datacore Solutions</h2>
    <p>Lorem ipsum dolor sit amet, consectetur adipiscing elit, sed do eiusmod tempor incididunt ul abo re et dolore magna aliquaenim ad minim veniam, quis nostrud exercitation ull loamco laboris nisi ut aliquip ex ea commodo cequatorem ipsum dolor sit amet, consectetur adipisicinloig elit, sedido eiusmod tempor incididunt ul abo re et dolore magna aliquaenim ad minim veniam, quis nostrud exercitation ullamco laboris nisi ut aliquip ex ea commodo cequatorem ipsum dolor sit amet loco nse ctetur adipiscing elit, sed do eiusmod tempor incididunt ul abo re et dolore magna aliqu alor eim ad minim veniam, quis nostrud exercitation ullamco laboris ni</p>
    <span class="btn">Read more <svg viewBox="0 0 10 10"><circle cx="5" cy="5" r="4.3" stroke="#fff" fill="none"/><path d="M4 3l2 2-2 2" stroke="#fff" fill="none"/></svg></span>
  </div>
</section>

<section class="recent">
  <div class="wrap">
    <h2><span class="accent">Recent</span> Recruitments</h2>
    <div class="cards">
      <article class="card"><div class="photo" role="img" aria-label="Interview between two people at a desk"></div><div class="body"><h4>Job Name</h4><p>Lorem ipsum dolor sit amet,lo cons ectetur adipiscing elit, sed.</p><span class="loc"><svg viewBox="0 0 8 10"><path d="M4 0a4 4 0 0 1 4 4c0 3-4 6-4 6S0 7 0 4a4 4 0 0 1 4-4z" fill="#c8202a"/><circle cx="4" cy="4" r="1.5" fill="#fff"/></svg>Location Name: Loremipsm</span></div></article>
      <article class="card"><div class="photo" role="img" aria-label="Handshake over a glass meeting table"></div><div class="body"><h4>Job Name</h4><p>Lorem ipsum dolor sit amet,lo cons ectetur adipiscing elit, sed.</p><span class="loc"><svg viewBox="0 0 8 10"><path d="M4 0a4 4 0 0 1 4 4c0 3-4 6-4 6S0 7 0 4a4 4 0 0 1 4-4z" fill="#c8202a"/><circle cx="4" cy="4" r="1.5" fill="#fff"/></svg>Location Name: Loremipsm</span></div></article>
      <article class="card"><div class="photo" role="img" aria-label="Team meeting in a bright office"></div><div class="body"><h4>Job Name</h4><p>Lorem ipsum dolor sit amet,lo cons ectetur adipiscing elit, sed.</p><span class="loc"><svg viewBox="0 0 8 10"><path d="M4 0a4 4 0 0 1 4 4c0 3-4 6-4 6S0 7 0 4a4 4 0 0 1 4-4z" fill="#c8202a"/><circle cx="4" cy="4" r="1.5" fill="#fff"/></svg>Location Name: Loremipsm</span></div></article>
      <article class="card"><div class="photo" role="img" aria-label="Job interview across a desk"></div><div class="body"><h4>Job Name</h4><p>Lorem ipsum dolor sit amet,lo cons ectetur adipiscing elit, sed.</p><span class="loc"><svg viewBox="0 0 8 10"><path d="M4 0a4 4 0 0 1 4 4c0 3-4 6-4 6S0 7 0 4a4 4 0 0 1 4-4z" fill="#c8202a"/><circle cx="4" cy="4" r="1.5" fill="#fff"/></svg>Location Name: Loremipsm</span></div></article>
    </div>
  </div>
</section>

<section class="clients">
  <div class="wrap">
    <svg class="arrow" viewBox="0 0 12 22"><path d="M11 1L1 11l10 10" stroke="#ccc" fill="none" stroke-width="1.5"/></svg>
    <div class="logos"><span>LUMORA</span><span>tavrix</span><span>Orbelta</span><span>Kestrel</span><span>ZENTHIC</span></div>
    <svg class="arrow" viewBox="0 0 12 22"><path d="M1 1l10 10L1 21" stroke="#ccc" fill="none" stroke-width="1.5"/></svg>
  </div>
</section>

<footer class="footer">
  <div class="wrap">
    <div class="about-col">
      <h4>KPV Datacore Solutions</h4>
      <p>Lorem ipsum dolor sit amet, ecur adipiscing elit, sed do eiusmod tem por incididunt ut labore et dolore magna aliquaenim ad minimam .Lorem ipsum dolor sit amet.</p>
    </div>
    <div class="contact-col">
      <h4>Quick Contact</h4>
      <ul>
        <li><svg viewBox="0 0 8 10"><path d="M4 0a4 4 0 0 1 4 4c0 3-4 6-4 6S0 7 0 4a4 4 0 0 1 4-4z" fill="#bbb"/></svg><span>18 Harbour Row London<br>E14 7QT</span></li>
        <li><svg viewBox="0 0 10 10"><path d="M2 0h2l1 3-1.5 1a6 6 0 0 0 2.5 2.5L7 5l3 1v2a2 2 0 0 1-2 2A8 8 0 0 1 0 2a2 2 0 0 1 2-2z" fill="#bbb"/></svg><span>Phone: 555-402-6618</span></li>
        <li><svg viewBox="0 0 10 8"><rect width="10" height="8" fill="#bbb"/><path d="M0 0l5 4 5-4" stroke="#3a3a3a" fill="none"/></svg><span>Email: info@ kpvmail.com</span></li>
      </ul>
    </div>
    <div class="map" role="img" aria-label="Street map of the office location by the docks"></div>
  </div>
</footer>

<div class="bottom">
  <div class="wrap">
    <div class="social"><i></i><i></i><i></i><i></i></div>
    <span>© 2016 KPV Datacore Solutions. All copyrights are reserved.</span>
  </div>
</div>

</body>
</html>
```